I need a design that promotes "A peak path hub for runners". services include assessment, massage, physiotherapy, pilates, suspension training, kinesiotaping in any combination.
I would like to bring the design into my website, flyers etc

Target Market(s)

athletes from beginner to elite - any age, male and female

Industry/Entity Type

Shop

Contact Information for Business Card

Peak-Path Hub for Runners
17 Corla Lane, Westmere, Tauranga
021 874 3061
tess.harlow@mailbrook.example

Logo Text

Logo styles of interest
Abstract Logo
Requirements
Nice to have
• Blue colour theme

```html
<!DOCTYPE html>
<html lang="en">
<head>
<meta charset="utf-8">
<title>Peak-Path Hub for Runners – Business Card</title>
<link rel="stylesheet" href="https://fonts.googleapis.com/css2?family=Michroma&family=Fira+Sans+Condensed:wght@400;600&display=swap">
<style>
  :root {
    --backdrop: #5e3520;
    --card-frame: #ffffff;
    --blue-glow: #3448a0;
    --blue-deep: #1f2262;
    --title-tint: #dfe6f6;
    --name-tint: #bcd0f2;
    --label-tint: #a9bde8;
    --text-white: #ffffff;
  }
  * { margin: 0; padding: 0; box-sizing: border-box; }
  html, body {
    width: 1200px; height: 1181px; overflow: hidden;
    background: var(--backdrop);
  }
  .card {
    position: absolute;
    left: 203px; width: 794px; height: 456px;
    background: var(--card-frame);
    padding: 10px;
    box-shadow: 0 4px 14px rgba(0,0,0,0.35);
  }
  .card--front { top: 101px; }
  .card--back  { top: 614px; }
  .card__face {
    position: relative;
    width: 100%; height: 100%;
    background: radial-gradient(ellipse 60% 65% at 50% 50%, var(--blue-glow) 0%, var(--blue-deep) 100%);
    overflow: hidden;
  }
  .tagline {
    position: absolute; left: 0; right: 0; top: 203px;
    text-align: center;
    font-family: "Michroma", sans-serif;
    font-size: 22px; letter-spacing: 1px;
    color: var(--title-tint);
    text-shadow: 0 2px 3px rgba(0,0,0,0.55);
    text-transform: uppercase;
  }
  .identity {
    position: absolute; right: 417px; top: 192px;
    text-align: right;
    font-family: "Fira Sans Condensed", sans-serif;
    line-height: 1;
  }
  .identity__name {
    font-weight: 600; font-size: 33px; letter-spacing: 1px;
    color: var(--name-tint);
  }
  .identity__role {
    margin-top: 1px;
    font-size: 16px; letter-spacing: 1px;
    color: var(--text-white);
  }
  .divider {
    position: absolute; left: 385px; top: 151px;
    width: 3px; height: 135px;
    background: var(--text-white);
  }
  .contact {
    position: absolute; left: 417px; top: 173px;
    font-family: "Fira Sans Condensed", sans-serif;
    font-size: 15.5px; line-height: 18.5px;
    color: var(--text-white);
    list-style: none;
  }
  .contact__label { color: var(--label-tint); display: inline-block; }
</style>
</head>
<body>
  <section class="card card--front">
    <div class="card__face">
      <p class="tagline">Peak-Path Hub for Runners</p>
    </div>
  </section>

  <section class="card card--back">
    <div class="card__face">
      <div class="identity">
        <p class="identity__name">YOUR NAME</p>
        <p class="identity__role">MANAGING DIRECTOR</p>
      </div>
      <div class="divider"></div>
      <ul class="contact">
        <li><span class="contact__label">Web&nbsp;&nbsp;&nbsp;:</span> www.peakpathhub.example</li>
        <li><span class="contact__label">Email :</span> tess.harlow@mailbrook.example</li>
        <li><span class="contact__label">Phone :</span> 021 874 3061</li>
        <li>17 Corla Lane, Westmere,</li>
        <li>Tauranga</li>
      </ul>
    </div>
  </section>
</body>
</html>
```